Sunset Harbor Living Web Page

We need a web page design that has two intro pages - first being a 'home page', then a link to the second page that has the 'content tabs' and a 'call to action' (see below).

The business helps people that wish to retire to S.E.Asia (Thailand, Malaysia, Indonesia,The Philippines etc) - to enjoy the lifestyle and the remaining years of their lives. What attracts S.E.Asia to many people is the lower cost, the atmoshpere and beauty of the tropics and the vibrancy of the various countries.

People that are wishing to make the most of their retirement and are adventurous at a great bargain compared to the cost of their own countries will be interested.

We help them achieve this - visa, financials (tax, gov't payments etc), introduce them to the right people for property, clubs, retirement facilities, insurance and so forth.

Therefore we are providing an extremely wide ranging service and this site will provide broad but general information only - with a call to action to come and see us for more specific information and how we can help them specifically.

This site will be predominantly for travel and lifestyle, it will be linked with another financial services (financial planning) site later down the track.

The colour scheme is dark green and blue - as per the attached logo design. Photos and background just think lifestyle and S.E.Asia - beaches/mountains/water/recreational activities for retirees.

Target market is mostly those coming up to retirement to those that are already retired. But we also expect to have some interest with younger people that would like to find out more and plan for the future. So a broad age group but I would say mostly 40-70 yrs old.

On the first (Home) page we would like our company name 'Sunset Harbor Living', our logo (which will be on all pages) and a statement such as: “Imagine a retirement where your dreams are brought to life, and you have never felt more alive. Let us show you how”. Then a link to the second page.

We would like an uncluttered site. On the second (contents) page the tabs would be:

- Visa
- Property
- Financials
- Travel
- Insurance & Healthcare
- Medical Tourism
- Cost of living
- Weekly Blogs and articles
- Sunset Harbor Living story

We would also like a call to action on the second page - asking them to leave their contact details if they wish to learn more or sign up to our weekly newsletter/blog.

We are open to suggestions and your imaginations.

Thank you
Malcolm

Font styles to use
Serif
Script

Colors
0255a3
3377b5
00a990
9bcb3c
abd036
33b8a4
85abd2
cadf82
86cfc6

Requirements
Must have
• I have been asked by the web designer to receive a 'Web Font' so that we can 'get off of Zentrofy'. Hope that makes sense.

```html
<!DOCTYPE html>
<html lang="en">
<head>
<meta charset="utf-8">
<title>Sunset Harbor Living</title>
<link href="https://fonts.googleapis.com/css2?family=Open+Sans:wght@400;600;700&family=Roboto:wght@300;400;500;700&display=swap" rel="stylesheet">
<style>
:root{
  --teal:#00a990;
  --teal-dark:#0f9e86;
  --blue:#0255a3;
  --blue-nav:#1f4fa0;
  --lime:#9bcb3c;
  --lime-light:#b8dc6a;
  --text:#555;
  --dark:#222;
  --line:#ddd;
  --white:#fff;
  --social-a:#2a5ab0;
  --social-b:#1d9fe0;
  --social-c:#e2522f;
}
*{margin:0;padding:0;box-sizing:border-box}
html,body{width:877px;height:1200px;overflow:hidden;background:var(--white)}
body{position:relative;font-family:"Roboto",sans-serif;color:var(--text)}
.abs{position:absolute}

/* header */
.brand{left:56px;top:20px;display:flex;align-items:center;gap:8px}
.brand-dot{width:30px;height:30px;border-radius:50%;background:var(--teal)}
.brand-name{font-family:"Open Sans",sans-serif;font-weight:700;font-size:15px;color:var(--blue);line-height:1.1;width:110px}
.search{left:499px;top:29px;width:112px;height:27px;border:1px solid #ccc;font-size:7px;color:#aaa;display:flex;align-items:center;padding-left:9px;gap:5px;letter-spacing:.5px}
.connect{left:635px;top:28px;font-size:7px;color:#aaa;letter-spacing:.3px}
.social{display:flex;gap:8px;margin-top:7px}
.social span{width:15px;height:15px;display:block}
.s1{background:var(--social-a)}.s2{background:var(--social-b)}.s3{background:var(--social-c)}
.call{left:746px;top:28px;font-size:7.5px;color:#aaa;letter-spacing:.3px}
.phone{display:flex;align-items:center;gap:5px;margin-top:5px;font-size:14px;color:var(--blue);font-weight:300}

/* nav */
.nav{left:0;top:82px;width:877px;height:23px;background:var(--teal);display:flex;align-items:center;padding-left:54px;font-family:"Open Sans",sans-serif;font-size:7.4px;font-weight:600;color:var(--white)}
.nav span{padding:0 10.5px;height:23px;line-height:23px}
.nav .active{background:var(--blue-nav)}

/* hero */
.hero{left:0;top:105px;width:877px;height:324px;background:linear-gradient(180deg,#e9e3d6 0%,#f3d9a2 40%,#c8b895 58%,#d9a35c 80%,#b67a3a 100%)}
.hero-caption{left:55px;top:292px;width:279px;height:137px;background:rgba(90,90,90,.6);color:var(--white);font-size:16.5px;font-weight:300;line-height:23px;padding:19px 0 0 27px}
.dots{left:398px;top:401px;display:flex;gap:11px;align-items:center}
.dots span{width:6px;height:6px;border-radius:50%;background:var(--white)}
.dots .ring{width:8px;height:8px;background:none;border:1px solid var(--white)}

/* welcome */
.h2{font-family:"Open Sans",sans-serif;font-weight:600;font-size:13px;color:var(--teal);letter-spacing:.2px}
.welcome-title{left:54px;top:457px}
.welcome-text{left:54px;top:483px;width:501px;font-size:8.3px;line-height:14.4px;text-align:justify}
.btn{display:inline-block;background:var(--teal);color:var(--white);font-family:"Open Sans",sans-serif;font-weight:700;font-size:7.4px;letter-spacing:.3px}
.welcome-btn{left:55px;top:539px;padding:5px 10px}
.logo-card{left:605px;top:455px;width:216px;height:104px;border:1px solid #ccc;box-shadow:0 3px 8px rgba(0,0,0,.12);display:flex;align-items:center;justify-content:center;gap:8px}

/* service tiles */
.tile{top:596px;width:250px;height:154px;color:var(--white);text-align:center;padding-top:14px}
.tile h3{font-family:"Open Sans",sans-serif;font-weight:600;font-size:12px;margin-top:6px;letter-spacing:.3px}
.tile p{font-size:7.6px;line-height:13px;margin:8px auto 0;width:210px;opacity:.92}
.tile .more{display:inline-block;margin-top:14px;padding:4px 12px;font-family:"Open Sans",sans-serif;font-weight:700;font-size:7px}
.t1{left:55px;background:var(--teal)}.t1 .more{background:#20b79e}
.t2{left:313px;background:var(--blue)}.t2 .more{background:#1e6fc0}
.t3{left:572px;background:var(--lime)}.t3 .more{background:var(--lime-light)}

/* blog */
.blog-title{left:53px;top:781px}
.blog-all{left:752px;top:779px;padding:5px 10px}
.post{top:808px;width:187px;height:188px;border:1px solid var(--line);box-shadow:0 1px 3px rgba(0,0,0,.08)}
.post-img{height:104px;position:relative}
.date{position:absolute;left:5px;bottom:8px;width:22px;height:26px;background:rgba(40,40,40,.8);color:var(--white);text-align:center;font-size:10px;font-weight:700;line-height:12px;padding-top:2px}
.date small{display:block;font-size:6px;font-weight:400;line-height:8px}
.post h4{font-size:8px;font-weight:500;color:var(--dark);margin:13px 0 0 13px}
.post p{font-size:7.3px;line-height:12px;margin:4px 13px 0 14px;text-align:justify;color:#666}
.post .more{margin:5px 0 0 14px;padding:2px 6px;background:var(--blue);font-size:6.2px}
.p1{left:55px}.p2{left:248px}.p3{left:442px}.p4{left:635px}
.i1{background:linear-gradient(180deg,#8cc0d0,#46c4b8 60%,#2aa59a)}
.i2{background:linear-gradient(135deg,#e6c77a,#b98a3f 50%,#3d5a66)}
.i3{background:linear-gradient(135deg,#6b8f55,#c9d07c 45%,#4c5b66)}
.i4{background:linear-gradient(180deg,#9a7fa7,#c9b6cf 55%,#6e7fb5)}

/* newsletter */
.news-title{left:0;top:1036px;width:877px;text-align:center}
.news-title span{display:inline-block;padding-bottom:5px;border-bottom:1px solid #bbb}
.field{top:1079px;width:185px;height:31px;border:1px solid #ccc;display:flex;align-items:center;padding-left:11px;gap:7px;font-size:7.3px;color:#555}
.f1{left:188px}.f2{left:384px}
.signup{left:580px;top:1079px;width:101px;height:31px;display:flex;align-items:center;justify-content:center;gap:6px;font-size:10px}

/* footer */
.footer{left:0;top:1141px;width:877px;height:59px;background:var(--teal);color:var(--white)}
.follow{left:55px;top:20px;display:flex;align-items:center;gap:14px;font-family:"Open Sans",sans-serif;font-weight:700;font-size:8.2px;letter-spacing:.3px}
.follow .social{margin:0;gap:4px}
.follow .social span{width:20px;height:20px}
.foot-links{right:56px;top:27px;font-size:7.2px}
</style>
</head>
<body>

<header>
  <div class="abs brand"><span class="brand-dot"></span><span class="brand-name">Sunset Harbor Living</span></div>
  <div class="abs search">
    <svg width="8" height="8" viewBox="0 0 10 10"><circle cx="4" cy="4" r="3" fill="none" stroke="#aaa" stroke-width="1.3"/><line x1="6.3" y1="6.3" x2="9" y2="9" stroke="#aaa" stroke-width="1.3"/></svg>SEARCH
  </div>
  <div class="abs connect">CONNECT WITH US
    <div class="social"><span class="s1"></span><span class="s2"></span><span class="s3"></span></div>
  </div>
  <div class="abs call">CALL US NOW ON
    <div class="phone">
      <svg width="10" height="10" viewBox="0 0 10 10"><path d="M2 1l2 2-1 1.5a6 6 0 002.5 2.5L7 6l2 2-1.5 1.5C4 9 1 6 .5 2.5z" fill="#0255a3"/></svg>1.800.555.0142
    </div>
  </div>
</header>

<nav class="abs nav">
  <span class="active">Home</span><span>Visa</span><span>Property</span><span>Financials</span><span>Travel</span><span>Insurance &amp; Healthcare</span><span>Medical Tourism</span><span>Cost of living</span><span>Weekly Blogs and articles</span><span>Sunset Harbor Living story</span><span>Contact us</span>
</nav>

<section>
  <div class="abs hero" role="img" aria-label="Retired couple holding hands on a tropical beach at sunset"></div>
  <div class="abs hero-caption">Imagine a retirement where your dreams are brought to life, and you have never felt more alive. Let us show you how</div>
  <div class="abs dots"><span></span><span class="ring"></span><span></span><span></span><span></span></div>
</section>

<section>
  <h2 class="abs h2 welcome-title">WELCOME TO OUR SITE</h2>
  <p class="abs welcome-text">There are many variations of passages of Lorem Ipsum available, but the majority have suffered alteration in some form, by injected humour, or randomised words which don't look even slightly believable. If you are going to use a passage of Lorem Ipsum. All the Lorem Ipsum generators on the Internet tend to repeat predefine Vivamus aliquet mi mi, a volutpat diam .</p>
  <span class="abs btn welcome-btn">READ MORE</span>
  <div class="abs logo-card"><span class="brand-dot"></span><span class="brand-name">Sunset Harbor Living</span></div>
</section>

<section>
  <div class="abs tile t1">
    <svg width="40" height="40" viewBox="0 0 40 40" fill="none" stroke="#fff" stroke-width="1.6"><circle cx="20" cy="20" r="18"/><ellipse cx="20" cy="20" rx="8" ry="18"/><line x1="2" y1="20" x2="38" y2="20"/><path d="M5 11h30M5 29h30"/></svg>
    <h3>TRAVEL</h3>
    <p>At vero eos et accusamus et iusto odio dignissimos ducimus qui blanditiis praesentium.</p>
    <span class="more">READ MORE</span>
  </div>
  <div class="abs tile t2">
    <svg width="40" height="40" viewBox="0 0 40 40" fill="none" stroke="#fff" stroke-width="1.8"><path d="M20 22l-7-7a4.5 4.5 0 017-5.5 4.5 4.5 0 017 5.5z" fill="#fff"/><path d="M4 20v8l9 8M36 20v8l-9 8M8 24l6 5M32 24l-6 5"/></svg>
    <h3>INSURANCE &amp; HEALTHCARE</h3>
    <p>At vero eos et accusamus et iusto odio dignissimos ducimus qui blanditiis praesentium.</p>
    <span class="more">READ MORE</span>
  </div>
  <div class="abs tile t3">
    <svg width="40" height="40" viewBox="0 0 40 40" fill="none" stroke="#fff" stroke-width="1.8"><rect x="8" y="6" width="24" height="30" rx="2"/><rect x="15" y="3" width="10" height="6" rx="1"/><path d="M12 22h5l2-5 3 9 2-4h4M12 30h16"/></svg>
    <h3>MEDICAL TOURISM</h3>
    <p>At vero eos et accusamus et iusto odio dignissimos ducimus qui blanditiis praesentium.</p>
    <span class="more">READ MORE</span>
  </div>
</section>

<section>
  <h2 class="abs h2 blog-title">LATEST BLOG</h2>
  <span class="abs btn blog-all">READ MORE</span>

  <article class="abs post p1">
    <div class="post-img i1" role="img" aria-label="Swimmer in clear turquoise water among limestone islands"><span class="date">02<small>JAN</small></span></div>
    <h4>But I must explain to you how</h4>
    <p>At vero eos et accusamus et iusto odio dignissimos ducimus.</p>
    <span class="btn more">READ MORE</span>
  </article>
  <article class="abs post p2">
    <div class="post-img i2" role="img" aria-label="Kayaking through splashing water in sunlight"><span class="date">04<small>JAN</small></span></div>
    <h4>On the other hand, we denounce</h4>
    <p>At vero eos et accusamus et iusto odio dignissimos ducimus.</p>
    <span class="btn more">READ MORE</span>
  </article>
  <article class="abs post p3">
    <div class="post-img i3" role="img" aria-label="Camping tent in a green forest"><span class="date">05<small>JAN</small></span></div>
    <h4>At vero eos et accusamus et iusto</h4>
    <p>At vero eos et accusamus et iusto odio dignissimos ducimus.</p>
    <span class="btn more">READ MORE</span>
  </article>
  <article class="abs post p4">
    <div class="post-img i4" role="img" aria-label="Group yoga class stretching on mats"><span class="date">06<small>JAN</small></span></div>
    <h4>But in certain circumstances</h4>
    <p>At vero eos et accusamus et iusto odio dignissimos ducimus.</p>
    <span class="btn more">READ MORE</span>
  </article>
</section>

<section>
  <h2 class="abs h2 news-title"><span>NEWSLETTER SIGNUP!</span></h2>
  <div class="abs field f1">
    <svg width="8" height="8" viewBox="0 0 10 10" fill="#555"><circle cx="5" cy="3" r="2.5"/><path d="M0 10a5 4 0 0110 0z"/></svg>Name
  </div>
  <div class="abs field f2">
    <svg width="9" height="7" viewBox="0 0 10 8" fill="none" stroke="#555"><rect x=".5" y=".5" width="9" height="7"/><path d="M.5 .5l4.5 4 4.5-4"/></svg>E mail id
  </div>
  <div class="abs btn signup">SIGNUP!
    <svg width="14" height="7" viewBox="0 0 14 7"><path d="M0 3.5h12M9 .5l3 3-3 3" stroke="#fff" stroke-width="1.5" fill="none"/></svg>
  </div>
</section>

<footer class="abs footer">
  <div class="abs follow">FOLLOW US ON
    <div class="social"><span class="s1"></span><span class="s2"></span><span class="s3"></span></div>
  </div>
  <div class="abs foot-links">Home &nbsp;|&nbsp; About us &nbsp;|&nbsp; Contact Us &nbsp;|&nbsp; Copyrights @ 2016 All Rights Reserved</div>
</footer>

</body>
</html>
```